Interior Design & consultancy firm requires a new business card design that is a little bit funky bu

Velbrook Design Services is a leading strategic design practice specialising in the development and implementation of strategies and design solutions for commercial workplaces across a wide variety of industries.

The company has over twenty years experience in the strategic design, development and construction of innovative and efficient workplace environments for the commercial, corporate and industrial sectors.

We believe good design and efficient workspaces can transform companies, improve people’s lives and increase productivity.

Target Market(s)

My clients are mainly Government or corporate clients wanting to create a statement with their office fitout & new furniture that reflects their corporate identity

Industry/Entity Type

Construction

Font styles to use
Sans Serif

Colors
add136

Requirements
Must have
• The business card must be easy to read, simple & highlight my name & mobile phone number
Should not have
• I do not want the card to be fussy, feature too many colours or look to busy.

```html
<!DOCTYPE html>
<html lang="en">
<head>
<meta charset="utf-8">
<title>Velbrook Design Services – Business Card</title>
<link rel="stylesheet" href="https://fonts.googleapis.com/css2?family=Montserrat:wght@300;400;700&display=swap">
<style>
  :root {
    --lime: #add136;
    --charcoal: #58595b;
    --white: #ffffff;
    --backdrop: #e9e9e7;
    --shadow: rgba(0, 0, 0, 0.18);
  }
  * { box-sizing: border-box; margin: 0; padding: 0; }
  html, body {
    width: 1200px;
    height: 1000px;
    overflow: hidden;
    background: var(--backdrop);
    font-family: "Montserrat", Arial, sans-serif;
  }
  .canvas {
    position: relative;
    width: 1200px;
    height: 1000px;
  }
  .card {
    position: absolute;
    top: 205px;
    width: 360px;
    height: 590px;
    border-radius: 4px;
    box-shadow: 0 14px 34px var(--shadow);
  }
  .card--front {
    left: 190px;
    background: var(--lime);
  }
  .card--back {
    left: 650px;
    background: var(--charcoal);
    padding: 46px 36px 0 36px;
    text-align: right;
  }

  /* front */
  .brand {
    position: absolute;
    left: 40px;
    right: 40px;
    top: 300px;
    display: flex;
    align-items: center;
    gap: 12px;
  }
  .brand__mark {
    flex: none;
    width: 14px;
    height: 14px;
    background: var(--white);
  }
  .brand__name {
    color: var(--white);
    font-weight: 300;
    font-size: 23px;
    letter-spacing: 0.5px;
    line-height: 1.2;
  }

  /* back */
  .services {
    list-style: none;
    color: var(--lime);
    font-weight: 700;
    font-size: 20px;
    line-height: 1.22;
    letter-spacing: 0.3px;
  }
  .services__item--spaced { margin-top: 22px; }

  .person { margin-top: 40px; }
  .person__name {
    color: var(--lime);
    font-weight: 300;
    font-size: 25px;
    line-height: 1.2;
  }
  .person__title {
    color: var(--white);
    font-weight: 700;
    font-size: 17px;
    letter-spacing: 0.4px;
    margin-top: 2px;
  }
  .person__mobile {
    color: var(--white);
    font-weight: 300;
    font-size: 24px;
    letter-spacing: 1px;
    margin-top: 26px;
  }

  .contact { margin-top: 38px; }
  .contact__email {
    color: var(--white);
    font-weight: 400;
    font-size: 12.5px;
  }
  .contact__web {
    color: var(--lime);
    font-weight: 400;
    font-size: 15.5px;
    letter-spacing: 0.3px;
    margin-top: 4px;
  }
</style>
</head>
<body>
<main class="canvas">
  <section class="card card--front" aria-label="Business card front">
    <div class="brand">
      <span class="brand__mark" aria-hidden="true"></span>
      <span class="brand__name">Velbrook Design Services</span>
    </div>
  </section>

  <section class="card card--back" aria-label="Business card back">
    <ul class="services">
      <li>interior design</li>
      <li>space planning</li>
      <li>furniture</li>
      <li class="services__item--spaced">project management</li>
    </ul>
    <div class="person">
      <p class="person__name">Marion Calloway</p>
      <p class="person__title">BA Interior Design</p>
      <p class="person__mobile">M: 0412 587 203</p>
    </div>
    <div class="contact">
      <p class="contact__email">marion@velbrookdesignservices.com.au</p>
      <p class="contact__web">www.velbrookdesigns.com.au</p>
    </div>
  </section>
</main>
</body>
</html>
```